PowerPoint Listing Presentation for Real Estate Agency

We need a PowerPoint presentation for a new real estate brokerage team.

[[[[[[submit 1-3 sample slides for review - i will provide feedback and you can make changes if you want to - we will not be deciding on a design prior to the deadline]]]]]

******ATTN: DESIGNERS, if your skills are webdesign then just look at this like a portable website or a brochure. it should be easy enough******

NOTE: we have all the data to put into the slides. You just need to come up with the design and layout. we have a sample design that we like and have provided.

This focus will be for the home listing side of the business (a presentation for home sellers to convince them to use our services). The data and slides will present our team and the benefits, in the best light, to use our services over that of other real estate agent applying for the job. This presentation will proved facts and benefits and describe our special and unique offerings that will show a home seller why we can sell their home for more money in less time and with the least amount of hassle. The main color scheme is Dark Blue and White (we want some additional colors included - based on your creativity. otherwise the presentation will too monotone). We would like to see the use of Statistical Graphs (3-D) - data provided. We have photos of our team and a new logo (the logo could have some minor adjustment to clean it up if necessary) - also uploaded. We have about 80-90% of the information that will be put into the slides and will need to work closely to get the design and data integrated into the presentation (should be easier then it sounds). We should be able to add slides and data 'at will' over time via our master slides built into the presentation. We have a pretty good sample presentation that we like and can be used as a guideline (this is from our affiliated business network and we have full rights to all the information), it is uploaded but doesn't contain all the slide because of size limitations.

NOTE: An additional buyers presentation will be needed after we get the sellers presentation completed, which means additional work.

This should be enough to get you started and we are available if you have any questions to help you with the project. there will be around 60-70 total slides. once concept is completed it will be easy to create the slides.

Target Market(s)

home sellers. people who are moving to a new and better home or relocation for job reasons. typically more established in life

Industry/Entity Type

Real Estate

Requirements
Must have
• all the slides must be congruent. in other words, the exact same layout feel should used across the board. we are working on building our trade dress/image. Also, it must have a soft and inviting overall feel, yet show strength of ability.
Nice to have
• nice to have use of real people images when necessary. 3D graphs would be nice. clean modern look and feel, yet sophisticated and professional.
Should not have
• should not have a lot of time consuming transitions. do not include 3D stick figures or distracting moving gifs

```html
<!DOCTYPE html>
<html lang="en">
<head>
<meta charset="utf-8">
<title>You'll Receive Superior Results</title>
<link href="https://fonts.googleapis.com/css2?family=PT+Serif:wght@400;700&display=swap" rel="stylesheet">
<style>
  :root {
    --navy: #0b2a5b;
    --navy-deep: #082350;
    --sky: #4d86d6;
    --gold: #f5b315;
    --orange: #f08c12;
    --title-blue: #2e6bc4;
    --ink: #111111;
    --text-navy: #0d2a5a;
    --paper: #ffffff;
    --mist: #e3ebf5;
  }
  * { margin: 0; padding: 0; box-sizing: border-box; }
  html, body { width: 1200px; height: 900px; overflow: hidden; background: var(--paper); }
  .slide {
    position: relative;
    width: 1200px;
    height: 900px;
    overflow: hidden;
    font-family: "PT Serif", Georgia, serif;
    background: radial-gradient(ellipse at 45% 40%, #ffffff 0%, #f3f6fb 55%, #e4ecf6 100%);
  }
  .backdrop { position: absolute; inset: 0; }
  .brand {
    position: absolute;
    left: 15px; top: 15px;
    width: 102px; height: 102px;
    background: var(--paper);
    border: 2px solid var(--navy);
    display: flex; align-items: center; justify-content: center;
    text-align: center;
    color: var(--navy);
    font-size: 17px;
    font-weight: 700;
    line-height: 1.2;
  }
  .headline {
    position: absolute;
    left: 508px; top: 46px;
    display: flex; align-items: center; gap: 18px;
    font-size: 41px;
    color: var(--ink);
    white-space: nowrap;
  }
  .headline-icon { width: 62px; height: 62px; flex: none; }
  .headline .accent { color: var(--title-blue); }
  .benefits {
    position: absolute;
    left: 68px; top: 322px;
    list-style: none;
  }
  .benefits li {
    display: flex; align-items: center; gap: 18px;
    height: 93px;
    font-size: 33px;
    color: var(--text-navy);
  }
  .bullet-icon { width: 48px; height: 52px; flex: none; }
  .house-art {
    position: absolute;
    right: 30px; bottom: 18px;
    width: 210px; height: 90px;
  }
</style>
</head>
<body>
<div class="slide">
  <svg class="backdrop" width="1200" height="900" viewBox="0 0 1200 900" aria-hidden="true">
    <rect x="70" y="200" width="1000" height="560" fill="var(--mist)" opacity="0.35"/>
    <!-- top-left corner band -->
    <path d="M0 0 H440 C320 70 130 180 0 315 Z" fill="var(--gold)"/>
    <path d="M0 0 H428 C310 68 122 174 0 305 Z" fill="var(--sky)"/>
    <path d="M0 0 H405 C295 62 115 162 0 288 Z" fill="var(--navy)"/>
    <!-- bottom-right corner band -->
    <path d="M1200 300 C1000 500 760 750 530 900 H1200 Z" fill="var(--gold)"/>
    <path d="M1200 310 C1005 510 770 760 545 900 H1200 Z" fill="var(--sky)"/>
    <path d="M1200 326 C1012 520 790 770 570 900 H1200 Z" fill="var(--navy-deep)"/>
  </svg>

  <div class="brand">Harlow<br>&amp; Reed</div>

  <h1 class="headline">
    <svg class="headline-icon" viewBox="0 0 62 62" aria-hidden="true">
      <circle cx="31" cy="31" r="29" fill="var(--navy)" stroke="#cfd9e8" stroke-width="3"/>
      <path d="M17 32 L31 19 L45 32" fill="none" stroke="#fff" stroke-width="3.5" stroke-linejoin="round"/>
      <rect x="22" y="31" width="18" height="13" fill="none" stroke="#fff" stroke-width="3"/>
    </svg>
    <span>You’ll Receive <span class="accent">Superior Results</span></span>
  </h1>

  <ul class="benefits">
    <li><svg class="bullet-icon" viewBox="0 0 48 52" aria-hidden="true"><ellipse cx="24" cy="47" rx="16" ry="3" fill="#d9dfe8"/><circle cx="24" cy="23" r="21" fill="var(--orange)"/><circle cx="24" cy="23" r="15" fill="var(--paper)"/><path d="M16 24 L24 17 L32 24 V31 H16 Z" fill="var(--navy)"/></svg>Our Unique Team System</li>
    <li><svg class="bullet-icon" viewBox="0 0 48 52" aria-hidden="true"><ellipse cx="24" cy="47" rx="16" ry="3" fill="#d9dfe8"/><circle cx="24" cy="23" r="21" fill="var(--orange)"/><circle cx="24" cy="23" r="15" fill="var(--paper)"/><path d="M16 24 L24 17 L32 24 V31 H16 Z" fill="var(--navy)"/></svg>Our Exclusive and Innovative Consumer Programs</li>
    <li><svg class="bullet-icon" viewBox="0 0 48 52" aria-hidden="true"><ellipse cx="24" cy="47" rx="16" ry="3" fill="#d9dfe8"/><circle cx="24" cy="23" r="21" fill="var(--orange)"/><circle cx="24" cy="23" r="15" fill="var(--paper)"/><path d="M16 24 L24 17 L32 24 V31 H16 Z" fill="var(--navy)"/></svg>Our Leading Edge Technology</li>
    <li><svg class="bullet-icon" viewBox="0 0 48 52" aria-hidden="true"><ellipse cx="24" cy="47" rx="16" ry="3" fill="#d9dfe8"/><circle cx="24" cy="23" r="21" fill="var(--orange)"/><circle cx="24" cy="23" r="15" fill="var(--paper)"/><path d="M16 24 L24 17 L32 24 V31 H16 Z" fill="var(--navy)"/></svg>Our Specialized Skill</li>
  </ul>

  <svg class="house-art" viewBox="0 0 210 90" role="img" aria-label="Row of three house outlines in white">
    <rect width="210" height="90" rx="6" fill="#1d3f75"/>
  </svg>
</div>
</body>
</html>
```